KRWB new business card design

We need a business card design for our established business which is Australia wide however based in Melbourne. We are a young team of Financial Planners who specialize in Insurance and Basic super advice for people like us.

We are people who help our clients get things done in a timely and cost effective manner whilst having a good time and a laugh along the way.

We would like this to have a consistent feel with our new e-brochure which i have attached from a color and font perspective.

Industry/Entity Type

Business

Requirements
Must have
• We do not need specific address details rather just the states we are in:

VIC/NSW/QLD/TAS
Nice to have
• Curved edge to mate the brochure

```html
<!DOCTYPE html>
<html lang="en">
<head>
<meta charset="utf-8">
<title>KRWB Financial — Business Card</title>
<link href="https://fonts.googleapis.com/css2?family=Arimo:wght@400;700&display=swap" rel="stylesheet">
<style>
  :root {
    --ink: #1e1e1e;
    --ink-soft: #2a2a2a;
    --leaf: #6cc04a;
    --leaf-deep: #00a651;
    --paper: #ffffff;
    --stage: #e4e6e5;
  }
  * { margin: 0; padding: 0; box-sizing: border-box; }
  html, body {
    width: 1200px; height: 900px; overflow: hidden;
    background: var(--stage);
    font-family: "Arimo", Arial, sans-serif;
  }
  .card {
    position: absolute;
    left: 290px;
    width: 620px; height: 360px;
    overflow: hidden;
    background: var(--ink);
    box-shadow: 0 8px 24px rgba(0,0,0,.18);
  }

  /* Back */
  .card--back {
    top: 60px;
    border-radius: 0 48px 0 48px;
    border-left: 14px solid var(--leaf);
  }
  .card--back .brand {
    position: absolute; top: 108px; left: 0; right: 0;
    display: flex; align-items: center; justify-content: center; gap: 14px;
  }
  .brand__mark { width: 26px; height: 26px; background: var(--leaf); }
  .brand__name {
    color: var(--paper); font-weight: 700; font-size: 40px; letter-spacing: 2px;
  }
  .card--back .tagline {
    position: absolute; bottom: 46px; left: 0; right: 0; text-align: center;
    color: var(--paper); font-size: 12px; letter-spacing: 3px; text-transform: uppercase;
  }

  /* Front */
  .card--front {
    top: 480px;
    border-radius: 0 0 0 48px;
    background: transparent;
    box-shadow: none;
  }
  .front__dark {
    position: absolute; inset: 0 330px 0 0;
    background: var(--ink);
    border-radius: 0 0 0 48px;
  }
  .front__panel {
    position: absolute; top: 0; right: 0; bottom: 0; width: 340px;
    background: var(--leaf);
    border-radius: 0 48px 48px 0;
  }
  .card--front .brand {
    position: absolute; top: 150px; left: 0; width: 290px;
    display: flex; align-items: center; justify-content: center; gap: 14px;
  }
  .card--front .brand__name { font-size: 44px; }

  .namebar {
    position: absolute; top: 72px; left: 240px; width: 340px; height: 60px;
    background: var(--ink-soft);
    padding: 10px 0 0 22px;
  }
  .namebar__name {
    color: var(--paper); font-size: 19px; letter-spacing: 2px; text-transform: uppercase;
  }
  .namebar__role { color: var(--leaf); font-size: 14px; letter-spacing: 1px; margin-top: 3px; }

  .contact {
    position: absolute; top: 175px; left: 310px;
    color: var(--ink); font-size: 13.5px; letter-spacing: .6px; line-height: 1.35;
  }
  .contact__regions { margin-bottom: 12px; }
  .contact__line { display: flex; align-items: center; gap: 9px; margin-top: 4px; }
  .contact__icon {
    width: 17px; height: 17px; background: var(--ink); flex: none;
    display: flex; align-items: center; justify-content: center;
  }
  .contact__value { font-size: 14.5px; }
</style>
</head>
<body>

<section class="card card--back" aria-label="Business card back">
  <div class="brand">
    <span class="brand__mark"></span>
    <span class="brand__name">KRWB</span>
  </div>
  <p class="tagline">Planning today, living tomorrow</p>
</section>

<section class="card card--front" aria-label="Business card front">
  <div class="front__dark"></div>
  <div class="front__panel"></div>

  <div class="brand">
    <span class="brand__mark"></span>
    <span class="brand__name">KRWB</span>
  </div>

  <div class="namebar">
    <p class="namebar__name">Daniel Archer</p>
    <p class="namebar__role">President</p>
  </div>

  <div class="contact">
    <p class="contact__regions">VIC / NSW / QLD / TAS<br>Advice Australia wide</p>
    <p class="contact__line">
      <span class="contact__icon">
        <svg width="11" height="11" viewBox="0 0 24 24"><path fill="#fff" d="M6.6 10.8c1.4 2.8 3.8 5.1 6.6 6.6l2.2-2.2c.3-.3.7-.4 1-.2 1.1.4 2.3.6 3.6.6.6 0 1 .4 1 1V20c0 .6-.4 1-1 1C10.6 21 3 13.4 3 4c0-.6.4-1 1-1h3.5c.6 0 1 .4 1 1 0 1.3.2 2.5.6 3.6.1.3 0 .7-.2 1z"/></svg>
      </span>
      <span class="contact__value">1300 555 014</span>
    </p>
    <p class="contact__line">
      <span class="contact__icon">
        <svg width="11" height="9" viewBox="0 0 22 16"><rect x="1" y="1" width="20" height="14" fill="none" stroke="#fff" stroke-width="2"/><path d="M1 1l10 8 10-8" fill="none" stroke="#fff" stroke-width="2"/></svg>
      </span>
      <span class="contact__value">admin@krwb.com.au</span>
    </p>
    <p class="contact__line">
      <span class="contact__icon">
        <svg width="11" height="11" viewBox="0 0 24 24"><circle cx="12" cy="12" r="9" fill="none" stroke="#fff" stroke-width="2"/><path d="M3 12h18M12 3c3 3 3 15 0 18M12 3c-3 3-3 15 0 18" fill="none" stroke="#fff" stroke-width="1.6"/></svg>
      </span>
      <span class="contact__value">www.krwbfinancial.com.au</span>
    </p>
  </div>
</section>

</body>
</html>
```